Stonebridge Building and Projects business cards

A business card with watermark background (construction work)

Company logo attached

Home improvement projects
House renovations
Bathroom and kitchen renovations
House extensions
New builds and granny flats

Director Omar Haddani
(Phone number)
omar@sbpbuilding.com.au
(Instagram logo) sbp_building

```html
<!DOCTYPE html>
<html lang="en">
<head>
<meta charset="utf-8">
<title>Stonebridge Building and Projects – Business Cards</title>
<link rel="stylesheet" href="https://fonts.googleapis.com/css2?family=Montserrat:wght@600;700&family=Arimo:wght@400;700&display=swap">
<style>
  :root {
    --brand-blue: #3276b8;
    --brand-blue-dark: #2b67a3;
    --ink: #333c44;
    --paper: #ffffff;
    --backdrop: #c9cacc;
    --watermark-light: #ececec;
  }
  * { box-sizing: border-box; margin: 0; padding: 0; }
  html, body { width: 1200px; height: 900px; overflow: hidden; }
  body {
    background: var(--backdrop);
    font-family: "Arimo", Arial, sans-serif;
    position: relative;
  }
  .card {
    position: absolute;
    left: 250px;
    width: 700px;
    height: 400px;
    border-radius: 34px;
    overflow: hidden;
    box-shadow: 0 6px 18px rgba(0,0,0,0.18);
  }
  .card--front { top: 40px; background: var(--brand-blue); color: var(--paper); }
  .card--back { top: 460px; background: var(--paper); color: var(--ink); }

  .watermark {
    position: absolute;
    right: 40px;
    top: 60px;
    width: 230px;
    height: 230px;
  }
  .card--front .watermark { background: var(--brand-blue-dark); }
  .card--back .watermark { background: var(--watermark-light); }

  /* front */
  .front-logo {
    position: absolute;
    left: 0; right: 0; top: 78px;
    text-align: center;
  }
  .wordmark {
    font-family: "Montserrat", sans-serif;
    font-weight: 700;
    display: inline-flex;
    align-items: center;
    gap: 12px;
  }
  .wordmark__square { width: 16px; height: 16px; display: inline-block; }
  .front-logo .wordmark { font-size: 30px; color: var(--paper); }
  .front-logo .wordmark__square { background: var(--paper); }
  .tagline {
    display: inline-block;
    margin-top: 10px;
    padding: 6px 8px 4px;
    border-top: 2px solid currentColor;
    font-size: 18px;
    text-decoration: underline;
    text-underline-offset: 3px;
  }
  .services {
    position: absolute;
    left: 0; right: 0; top: 228px;
    text-align: center;
    font-size: 19px;
    line-height: 1.45;
  }

  /* back */
  .back-logo { position: absolute; left: 52px; top: 62px; }
  .back-logo .wordmark { font-size: 26px; color: var(--brand-blue); }
  .back-logo .wordmark__square { background: var(--brand-blue); }
  .back-logo .tagline { color: var(--brand-blue); font-size: 16px; margin-left: 28px; }
  .person { position: absolute; left: 52px; top: 200px; }
  .person__name {
    font-family: "Montserrat", sans-serif;
    font-weight: 700;
    font-size: 27px;
    color: var(--brand-blue);
  }
  .person__role { font-size: 19px; margin-top: 2px; }
  .contact { list-style: none; margin-top: 14px; font-size: 17px; }
  .contact li { display: flex; align-items: center; gap: 10px; margin-top: 5px; }
  .contact svg { width: 16px; height: 16px; flex: none; }
  .contact .accent { color: var(--brand-blue); }
  .social {
    position: absolute;
    right: 44px; bottom: 54px;
    font-size: 17px;
  }
</style>
</head>
<body>

  <section class="card card--front" aria-label="Business card front">
    <div class="watermark" role="img" aria-label="Faint construction watermark"></div>
    <div class="front-logo">
      <div class="wordmark"><span class="wordmark__square"></span>Stonebridge Building and Projects</div><br>
      <span class="tagline">Solid from the ground up!</span>
    </div>
    <p class="services">
      Home improvement projects | House renovations<br>
      Bathroom and kitchen renovations<br>
      House extensions | New builds and granny flats
    </p>
  </section>

  <section class="card card--back" aria-label="Business card back">
    <div class="watermark" role="img" aria-label="Faint construction watermark"></div>
    <div class="back-logo">
      <div class="wordmark"><span class="wordmark__square"></span>Stonebridge Building and Projects</div><br>
      <span class="tagline">Solid from the ground up!</span>
    </div>
    <div class="person">
      <h1 class="person__name">Omar Haddani</h1>
      <p class="person__role">Director</p>
      <ul class="contact">
        <li>
          <svg viewBox="0 0 16 16" aria-hidden="true"><path d="M3 1.5l3 3-1.6 1.8a9 9 0 0 0 5.3 5.3L11.5 10l3 3-2 2C6.5 14.5 1.5 9.5 1 3.5z" fill="#3276b8"/></svg>
          044-555 018 274
        </li>
        <li>
          <svg viewBox="0 0 16 16" aria-hidden="true"><rect x="1" y="3" width="14" height="10" fill="#3276b8"/><path d="M1 3l7 6 7-6" fill="none" stroke="#fff" stroke-width="1.4"/></svg>
          omar@sbpbuilding.com.au
        </li>
        <li>
          <svg viewBox="0 0 16 16" aria-hidden="true"><g fill="none" stroke="#3276b8" stroke-width="1.4"><circle cx="8" cy="8" r="6.5"/><ellipse cx="8" cy="8" rx="3" ry="6.5"/><path d="M1.5 8h13"/></g></svg>
          <span>www.<span class="accent">sbpbuilding</span>.com.au</span>
        </li>
      </ul>
    </div>
    <p class="social">sbp_building</p>
  </section>

</body>
</html>
```